National Mission Critical Construction Contractor needs Stationery Design to make a bold statement

We are a small commercial construction company, working primarily in mission critical facilities across the U.S.. We have exciting corporate changes going an and a new logo and office space so we need new stationery. The final design should incorporate our new logo and invoke a fresh, high-tech feel while looking simple and modern.

Industry/Entity Type

Construction

Contact Information for Business Card

We are required to list our state licensing qualifications on the back of our card.

Font styles to use
Sans Serif

Requirements
Must have
• We need to have a design for second page of stationery, envelopes both standard and with a window and for a 3 x 4 notepad.

```html
<!DOCTYPE html>
<html lang="en">
<head>
<meta charset="utf-8">
<title>Northvale Construction – Business Card</title>
<link rel="stylesheet" href="https://fonts.googleapis.com/css2?family=Didact+Gothic&family=Montserrat:wght@600;700&display=swap">
<style>
  :root {
    --brand-blue: #2169b2;
    --brand-blue-deep: #1d5fa3;
    --brand-green: #8cbb2a;
    --paper: #f4f6f8;
    --ink: #3a3d42;
    --backdrop: #dcdcea;
    --white: #ffffff;
  }
  * { margin: 0; padding: 0; box-sizing: border-box; }
  html, body { width: 1200px; height: 906px; overflow: hidden; }
  body {
    background: var(--backdrop);
    font-family: "Didact Gothic", "Century Gothic", sans-serif;
    color: var(--ink);
    position: relative;
  }
  .card {
    position: absolute;
    width: 540px;
    height: 308px;
    border-radius: 3px;
    overflow: hidden;
    box-shadow: 0 6px 18px rgba(40, 40, 90, 0.18);
  }

  /* Back side */
  .card-back {
    left: 60px; top: 130px;
    background: var(--brand-blue);
    color: var(--white);
  }
  .card-back .wordmark {
    position: absolute; left: 46px; top: 62px;
    display: flex; align-items: center; gap: 14px;
  }
  .card-back .wordmark-dot {
    width: 50px; height: 50px; border-radius: 50%;
    border: 3px solid var(--white);
  }
  .card-back .wordmark-name {
    font-family: "Didact Gothic", sans-serif;
    font-size: 24px; letter-spacing: 1px; color: var(--white);
  }
  .card-back .faint-ring {
    position: absolute; left: 330px; top: 70px;
    width: 300px; height: 300px; border-radius: 50%;
    border: 10px solid rgba(255, 255, 255, 0.08);
  }
  .card-back .web {
    position: absolute; left: 46px; bottom: 40px;
    font-size: 14px; letter-spacing: 0.6px;
  }

  /* Front side */
  .card-front {
    left: 600px; top: 470px;
    background: var(--paper);
  }
  .side-band {
    position: absolute; left: 0; top: 0; bottom: 0; width: 58px;
    background: var(--brand-blue);
  }
  .side-stripe {
    position: absolute; left: 58px; top: 0; bottom: 0; width: 14px;
    background: var(--brand-green);
  }
  .icon-tab {
    position: absolute; left: 40px; top: 196px;
    width: 44px; height: 70px;
    background: var(--brand-blue);
    border-radius: 0 10px 10px 0;
    display: flex; flex-direction: column; align-items: center;
    justify-content: center; gap: 6px;
  }
  .icon-tab svg { width: 12px; height: 12px; }
  .front-wordmark {
    position: absolute; left: 42px; top: 78px;
    display: flex; align-items: center; gap: 12px;
  }
  .front-wordmark-dot {
    width: 62px; height: 62px; border-radius: 50%;
    background: var(--brand-blue);
    box-shadow: 0 0 0 6px var(--paper);
  }
  .front-wordmark-name {
    font-size: 28px; letter-spacing: 1px; color: var(--brand-blue);
  }
  .person {
    position: absolute; right: 34px; top: 36px; text-align: right;
  }
  .person-name {
    font-family: "Montserrat", sans-serif; font-weight: 700;
    font-size: 17px; letter-spacing: 0.5px; color: var(--brand-blue);
  }
  .person-role { font-size: 14px; margin-top: 2px; }
  .contact {
    position: absolute; left: 100px; top: 204px;
    font-size: 14px; line-height: 19px;
  }
  .address {
    position: absolute; right: 34px; top: 212px;
    font-size: 14px; line-height: 19px; text-align: right;
  }
</style>
</head>
<body>

  <section class="card card-back" aria-label="Business card back">
    <div class="faint-ring"></div>
    <div class="wordmark">
      <div class="wordmark-dot"></div>
      <span class="wordmark-name">NORTHVALE CONSTRUCTION</span>
    </div>
    <p class="web">www.northvale.example</p>
  </section>

  <section class="card card-front" aria-label="Business card front">
    <div class="side-band"></div>
    <div class="side-stripe"></div>

    <div class="front-wordmark">
      <div class="front-wordmark-dot"></div>
      <span class="front-wordmark-name">NORTHVALE CONSTRUCTION</span>
    </div>

    <div class="person">
      <p class="person-name">JORDAN ELLIS</p>
      <p class="person-role">General Manager</p>
    </div>

    <div class="icon-tab" aria-hidden="true">
      <svg viewBox="0 0 12 12"><path d="M3 1l2 2.5-1.2 1.2c.7 1.4 1.8 2.5 3.2 3.2L8.2 6.7 11 8.5 9.8 11C5 10.5 1.5 7 1 2.2z" fill="#fff"/></svg>
      <svg viewBox="0 0 12 12"><rect x="1" y="2.5" width="10" height="7" fill="none" stroke="#fff" stroke-width="1.2"/><path d="M1 2.5l5 4 5-4" fill="none" stroke="#fff" stroke-width="1.2"/></svg>
      <svg viewBox="0 0 12 12"><circle cx="6" cy="6" r="5" fill="none" stroke="#fff" stroke-width="1.1"/><ellipse cx="6" cy="6" rx="2.2" ry="5" fill="none" stroke="#fff" stroke-width="1"/><path d="M1 6h10" stroke="#fff" stroke-width="1"/></svg>
    </div>

    <div class="contact">
      <p>(555) 014-2290</p>
      <p>info@northvale.example</p>
      <p>www.northvale.example</p>
    </div>

    <div class="address">
      <p>1280 Harbor Lane NW</p>
      <p>Suite 210, Westbrook</p>
    </div>
  </section>

</body>
</html>
```